Exciting & Elegant Stationary Pack

Stationary consists of
1. Letter head / Envelope
2. Business Card
3. Invoice
4. 40x40mm sticker

Attached files;

1. Logo (Other formats available on request)
2. MS word Doc - For information and description of design
3. Website image (This will be our new website so use the colours so everything ties together)
4. Sample of stationary pack we like, but feel free to be creative

Target Market(s)

Home improvement

Industry/Entity Type

Construction

Font styles to use
Other font styles liked:
• Leave up to designer - We like font used on (website attached image)

Requirements
Must have
• Please look at uploaded file of sample website and use colours
Nice to have
• Any type of business card design - eg. metal, die cut, embossed, etc...

```html
<!DOCTYPE html>
<html lang="en">
<head>
<meta charset="utf-8">
<title>Grout &amp; Level — Stationery Pack</title>
<link href="https://fonts.googleapis.com/css2?family=Open+Sans:wght@400;600;700;800&display=swap" rel="stylesheet">
<style>
:root{
  --stage:#a9a7a8;
  --navy:#1b4a6b;
  --navy-deep:#153e5c;
  --red:#cf2a32;
  --sky:#9dc3e4;
  --paper:#f0efee;
  --paper-white:#f7f6f5;
  --ink:#2b2b2b;
  --rule:#2f5f86;
  --row:#c9cfd8;
}
*{box-sizing:border-box;margin:0;padding:0}
html,body{width:1200px;height:838px;overflow:hidden}
body{background:var(--stage);font-family:"Open Sans",Arial,sans-serif;color:var(--ink);position:relative}
.piece{position:absolute;box-shadow:0 1px 4px rgba(0,0,0,.25);overflow:hidden}
.band{position:absolute}
.band--red{background:var(--red)}
.band--sky{background:var(--sky)}
.brand{position:absolute;font-weight:800;color:var(--navy);letter-spacing:.5px;white-space:nowrap;line-height:1}
.brand--light{color:#fff}

/* folder */
.folder{left:44px;top:50px;width:376px;height:531px;background:linear-gradient(160deg,#20557a,var(--navy-deep))}
.folder .brand{left:120px;top:366px;font-size:26px}

/* letterhead & invoice shared header */
.sheet{top:91px;width:348px;height:490px;background:var(--paper)}
.letter{left:435px}
.invoice{left:807px}
.sheet .brand{left:28px;top:34px;font-size:15px}
.sheet .band--red{left:0;top:59px;width:120px;height:22px}
.sheet .band--sky{left:0;top:81px;width:120px;height:20px}
.contact{position:absolute;left:137px;top:60px;font-size:6.6px;line-height:10.6px;color:#222}
.contact p{display:flex;align-items:center;gap:4px}
.ico{width:7px;height:7px;flex:none}

.letter-body{position:absolute;left:26px;top:143px;width:298px}
.salute{font-size:9px;color:#444;margin-bottom:14px}
.letter-body .para{font-size:4.6px;line-height:8.2px;color:#444;margin-bottom:8px;text-align:justify}
.signoff{font-size:4.8px;color:#444;margin-top:16px}
.sig-area{width:46px;height:18px;background:#dcdad8;margin:6px 0 4px 12px}
.signer{font-size:5px;line-height:9px;color:#555;margin-left:12px}

/* invoice form */
.inv-label{position:absolute;font-size:5.5px;font-weight:700;color:var(--rule)}
.inv-field{position:absolute;font-size:5.5px;color:#333;display:flex;align-items:flex-end;gap:3px}
.inv-field .line{border-bottom:.6px solid var(--rule);flex:1;height:5px}
.inv-table{position:absolute;left:25px;top:173px;width:296px;height:242px;border:.8px solid var(--rule)}
.inv-head{position:relative;display:grid;grid-template-columns:25px 193px 39px 39px;height:14px;background:var(--navy);color:#fff;font-size:5.5px;font-weight:700;align-items:center}
.inv-head span{text-align:center}
.inv-head span:first-child{text-align:left;padding-left:5px}
.inv-rows{position:absolute;left:0;right:0;top:14px;bottom:0;background:repeating-linear-gradient(#f0efee 0 13.6px,var(--row) 13.6px 27.2px)}
.col-rule{position:absolute;top:14px;bottom:0;width:.6px;background:var(--rule)}
.pay-methods{position:absolute;left:38px;top:423px;width:200px;display:flex;justify-content:space-between;font-size:5.5px}
.totals{position:absolute;left:243px;top:414px;width:78px;border:.8px solid var(--rule);border-top:none}
.totals div{display:grid;grid-template-columns:39px 39px;height:14px;border-top:.6px solid var(--rule)}
.totals span{font-size:5.2px;font-weight:700;text-align:center;line-height:13px;border-right:.6px solid var(--rule)}
.accept{position:absolute;left:25px;top:443px;font-size:4.4px;line-height:6.5px;color:#444}

/* business cards */
.card-front{left:46px;top:595px;width:152px;height:87px;background:#fff}
.card-front .brand{left:10px;top:15px;font-size:10px}
.card-front .band--red{left:0;top:39px;width:152px;height:13px}
.card-front .band--sky{left:0;top:52px;width:152px;height:35px}
.card-name{position:absolute;right:10px;top:40px;text-align:right;color:#fff;font-size:5.2px;font-weight:700;line-height:6px}
.card-name small{display:block;font-size:3.2px;font-weight:400}
.card-info{position:absolute;right:10px;top:58px;text-align:right;font-size:3.6px;line-height:6px;color:var(--navy-deep)}
.card-back{left:42px;top:694px;width:153px;height:86px;background:var(--navy)}
.card-back .texture{position:absolute;inset:0;background:linear-gradient(135deg,#234f72,#1a4565)}
.card-back .brand{right:10px;bottom:22px;font-size:9px}

/* envelopes */
.env-front{left:211px;top:603px;width:391px;height:177px;background:var(--paper-white)}
.env-front .brand{left:24px;top:20px;font-size:13px}
.env-front .band--red{left:0;top:50px;width:110px;height:22px}
.env-front .band--sky{left:0;top:72px;width:110px;height:20px}
.env-address{position:absolute;left:125px;top:75px;font-size:6.6px;line-height:9.6px;color:#333}
.env-back{left:614px;top:605px;width:392px;height:178px;background:var(--paper-white)}
.flap{position:absolute;left:0;top:0;width:392px;height:57px;background:var(--navy);border-radius:0 0 10px 10px}
.flap .brand{left:170px;top:14px;font-size:9px}

/* sticker */
.sticker{left:1025px;top:623px;width:156px;height:157px;background:#fff}
.sticker .brand{left:18px;top:50px;font-size:12px}
.sticker .band--red{left:0;top:84px;width:156px;height:24px}
.sticker .band--sky{left:0;top:108px;width:156px;height:49px}
.sticker-info{position:absolute;right:14px;top:125px;text-align:right;font-size:6.6px;line-height:9.6px;color:var(--navy-deep)}
.sticker-info p{display:flex;align-items:center;justify-content:flex-end;gap:3px}
</style>
</head>
<body>

<svg width="0" height="0" style="position:absolute">
  <defs>
    <symbol id="i-phone" viewBox="0 0 10 10"><rect x="2.5" y="0.5" width="5" height="9" rx="1" fill="none" stroke="currentColor" stroke-width="1.2"/><rect x="4" y="7.3" width="2" height="1" fill="currentColor"/></symbol>
    <symbol id="i-pin" viewBox="0 0 10 10"><path d="M5 9.6C2.6 6.8 1.6 5.2 1.6 3.8a3.4 3.4 0 0 1 6.8 0c0 1.4-1 3-3.4 5.8z" fill="currentColor"/><circle cx="5" cy="3.8" r="1.3" fill="#fff"/></symbol>
    <symbol id="i-globe" viewBox="0 0 10 10"><circle cx="5" cy="5" r="4.2" fill="currentColor"/><path d="M1 5h8M5 1c-2 2.5-2 5.5 0 8M5 1c2 2.5 2 5.5 0 8" stroke="#fff" stroke-width=".7" fill="none"/></symbol>
  </defs>
</svg>

<!-- Presentation folder -->
<section class="piece folder">
  <div class="band band--red" style="left:0;top:433px;width:376px;height:49px"></div>
  <div class="band band--sky" style="left:0;top:482px;width:376px;height:49px"></div>
  <div class="brand brand--light">GROUT &amp; LEVEL</div>
</section>

<!-- Letterhead -->
<section class="piece sheet letter">
  <div class="brand">GROUT &amp; LEVEL</div>
  <div class="band band--red"></div>
  <div class="band band--sky"></div>
  <div class="contact">
    <p>ABN : 12 345 678 901</p>
    <p><svg class="ico"><use href="#i-phone"/></svg>0400 555 019</p>
    <p><svg class="ico"><use href="#i-pin"/></svg>PO BOX 48 HILLCREST NSW 2170</p>
    <p><svg class="ico"><use href="#i-globe"/></svg>www.groutandlevel.com.au</p>
  </div>
  <div class="letter-body">
    <p class="salute">Dear Mr. Carter,</p>
    <p class="para">Thank you for choosing us for your bathroom and kitchen renovation. This letter confirms the scope of tiling work we discussed during our site visit last week, including floor preparation, waterproofing and wall tiling to full height. All materials will be supplied by our team and checked on arrival.</p>
    <p class="para">Work is planned to begin on the first Monday of next month and should take about two weeks. Our crew will arrive each day at seven and leave the site clean and safe every afternoon.</p>
    <p class="para">Please let us know if you would like to change any tile selections before ordering. Samples of grout colours and trims can be dropped off at your home for you to compare in your own light. A deposit of twenty percent secures your booking in our schedule.</p>
    <p class="para">We look forward to working with you and are happy to answer any questions by phone or email at any time.</p>
    <p class="signoff">Sincerely,</p>
    <div class="sig-area" role="img" aria-label="Handwritten signature"></div>
    <p class="signer">Alex Carter<br>CEO/ Founder</p>
  </div>
</section>

<!-- Invoice -->
<section class="piece sheet invoice">
  <div class="brand">GROUT &amp; LEVEL</div>
  <div class="band band--red"></div>
  <div class="band band--sky"></div>
  <div class="contact">
    <p>ABN : 12 345 678 901</p>
    <p><svg class="ico"><use href="#i-phone"/></svg>0400 555 019</p>
    <p><svg class="ico"><use href="#i-pin"/></svg>PO BOX 48 HILLCREST NSW 2170</p>
    <p><svg class="ico"><use href="#i-globe"/></svg>www.groutandlevel.com.au</p>
  </div>
  <div class="inv-label" style="left:25px;top:124px">INVOICE # :</div>
  <div class="inv-label" style="left:247px;top:124px">DATE :</div>
  <div class="inv-field" style="left:25px;top:135px;width:296px">Customer:<span class="line"></span></div>
  <div class="inv-field" style="left:25px;top:148px;width:296px">Address :<span class="line"></span></div>
  <div class="inv-field" style="left:25px;top:161px;width:180px">Phone :<span class="line"></span></div>
  <div class="inv-field" style="left:211px;top:161px;width:110px">Fax :<span class="line"></span></div>
  <div class="inv-table">
    <div class="inv-rows"></div>
    <div class="inv-head"><span>QTY</span><span>DESCRIPTION</span><span>PRICE</span><span>AMOUNT</span></div>
    <div class="col-rule" style="left:25px"></div>
    <div class="col-rule" style="left:218px"></div>
    <div class="col-rule" style="left:257px"></div>
  </div>
  <div class="pay-methods">
    <span>VISA</span><span>MC</span><span>DEBIT</span><span>CASH</span><span>CHEQUE</span>
  </div>
  <div class="totals">
    <div><span>SUB TOTAL</span><span></span></div>
    <div><span>GST #</span><span></span></div>
    <div><span>SUBTOTAL</span><span></span></div>
  </div>
  <p class="accept">Signature Indicates<br>Acceptance of Price and term</p>
</section>

<!-- Business card front -->
<section class="piece card-front">
  <div class="brand">GROUT &amp; LEVEL</div>
  <div class="band band--red"></div>
  <div class="band band--sky"></div>
  <div class="card-name">Dara Quinn<small>Project Manager</small></div>
  <div class="card-info">Lic No. 204518c<br>0400 555 019<br>info@groutandlevel.com.au<br>www.groutandlevel.com.au</div>
</section>

<!-- Business card back -->
<section class="piece card-back">
  <div class="texture" role="img" aria-label="Navy tiled brick wall texture"></div>
  <div class="brand brand--light">GROUT &amp; LEVEL</div>
</section>

<!-- Envelope front -->
<section class="piece env-front">
  <div class="brand">GROUT &amp; LEVEL</div>
  <div class="band band--red"></div>
  <div class="band band--sky"></div>
  <p class="env-address">PO BOX 48 HILLCREST<br>NSW 2170</p>
</section>

<!-- Envelope back -->
<section class="piece env-back">
  <div class="flap"><div class="brand brand--light">GROUT &amp; LEVEL</div></div>
</section>

<!-- Sticker -->
<section class="piece sticker">
  <div class="brand">GROUT &amp; LEVEL</div>
  <div class="band band--red"></div>
  <div class="band band--sky"></div>
  <div class="sticker-info">
    <p>0400 555 019<svg class="ico"><use href="#i-phone"/></svg></p>
    <p>PO Box 48 Hillcrest NSW 2170<svg class="ico"><use href="#i-pin"/></svg></p>
  </div>
</section>

</body>
</html>
```